Brisk Hollow toothpaste tube design

Design a Brisk Hollow tube design for our all natural toothpaste. The toothpaste is 100% natural with a smooth marshmallow consistency. It's unique because it's not pastelike at all. The all natural flavors make the toothpaste taste great. The toothpaste is smooth yet still leaves your mouth feeling squeaky clean. We want to market this as an all natural family toothpaste.

The flavor is Mint. (possibly called "Breezy Mint")

We have included our logo (eps & jpg), information that goes on the back of the tube, and the artwork template from the tube supplier for the 4.2oz tube.

We like a vintage earthy retro look and feel but we are not limited to this.

The tubes stand upright as shown in the picture of File 4.
Updates

The finished artwork must include anĀ adobe illustratorĀ file.

I would like to thank all of the designers for their work on this project. We had a difficult time making a decision since all of the designs were very close to what we expected.

Sincerely,

Glen

Target Market(s)

The target market is families that desire an all natural toothpaste. We will be stressing the 100% natural and great taste.

Requirements
Must have
• Three colors maximum due to tube manufacture restrictions.

Must have "100% natural" and "fluoride free" on front of tube. A reference to the great taste or flavor is also important.

Must say 4.2 oz on the front of the tube, centered, at the bottom.
Nice to have
• Fun, colorful packaging that will stand out. Go to your local store and stand in front of the tootpaste shelves, give us something different!
Should not have
• We do not want a lot of red or blue because these are predominate colors already in use on toothpaste tubes and boxes.

```html
<!DOCTYPE html>
<html lang="en">
<head>
<meta charset="utf-8">
<title>Brisk Hollow – Breezy Mint tube artwork</title>
<link rel="stylesheet" href="https://fonts.googleapis.com/css2?family=Alegreya+Sans:wght@500;700;800&family=Kalam:wght@700&display=swap">
<style>
  :root {
    --canvas: #f3f3f1;
    --tube-white: #ffffff;
    --green-deep: #2e8a3d;
    --green-mid: #3f9b48;
    --green-pale: #cfe5c9;
    --green-text: #36953f;
    --crimp: #ececea;
  }
  * { box-sizing: border-box; margin: 0; padding: 0; }
  html, body { width: 1200px; height: 898px; overflow: hidden; background: var(--canvas); }
  body { font-family: "Alegreya Sans", Arial, sans-serif; }

  .artboard {
    position: relative; width: 1200px; height: 898px;
    display: flex; justify-content: center; align-items: center; gap: 110px;
  }
  .tube {
    position: relative; width: 400px; height: 790px;
    background: var(--tube-white);
    box-shadow: 0 2px 10px rgba(0,0,0,.08);
    display: flex; flex-direction: column; overflow: hidden;
  }
  .tube__crimp {
    height: 34px; flex: none;
    background: repeating-linear-gradient(90deg, var(--crimp) 0 3px, #f7f7f5 3px 6px);
  }
  .tube__cap-zone { height: 78px; flex: none; background: var(--tube-white); border-top: 1px solid #eee; }

  /* Brand name block */
  .brand {
    display: flex; align-items: center; justify-content: center; gap: 10px;
    color: var(--green-text); font-weight: 800; line-height: 1;
  }
  .brand__dot { width: 18px; height: 18px; border-radius: 50%; background: var(--green-text); flex: none; }
  .brand--front { font-size: 54px; margin: 70px 0 0; }
  .brand--back { font-size: 34px; margin: 48px 0 26px; }

  /* Front */
  .front__upper { flex: 1 1 auto; display: flex; flex-direction: column; }
  .tagline-band {
    margin-top: 64px; background: var(--green-pale);
    color: #fff; text-align: center; font-weight: 700; font-size: 19px; line-height: 1.2;
    padding: 16px 34px;
  }
  .flavour-band {
    background: var(--green-deep); color: #f4f8ef; text-align: center;
    font-family: "Kalam", cursive; font-size: 42px; padding: 8px 0 6px;
    border-bottom: 2px solid #bfe0b8;
  }
  .leaf-field {
    position: relative; height: 250px; flex: none;
    background: radial-gradient(ellipse at 70% 35%, var(--green-mid), var(--green-deep) 70%);
  }
  .badge {
    position: absolute; left: 20px; top: 40px; width: 118px; height: 118px;
    border-radius: 50%; border: 3px solid #fff; outline: 2px solid #fff; outline-offset: -10px;
    display: flex; flex-direction: column; align-items: center; justify-content: center;
    color: #fff; font-weight: 800; font-size: 15px; line-height: 1.15; text-align: center;
  }
  .net-weight {
    position: absolute; bottom: 16px; left: 0; right: 0; text-align: center;
    color: #fff; font-weight: 700; font-size: 21px;
  }

  /* Back */
  .back__body {
    flex: 1 1 auto; padding: 0 60px; text-align: center;
    color: var(--green-text); font-weight: 700; font-size: 14.5px; line-height: 1.3;
  }
  .back__body p + p { margin-top: 16px; }
</style>
</head>
<body>
<main class="artboard">

  <section class="tube tube--front" aria-label="Front of tube">
    <div class="tube__crimp"></div>
    <div class="front__upper">
      <div class="brand brand--front"><span class="brand__dot"></span>Brisk Hollow</div>
      <p class="tagline-band">An all natural flavoured toothpaste for the whole family with a smooth, great taste.</p>
      <h1 class="flavour-band">breezy mint</h1>
      <div class="leaf-field" role="img" aria-label="Large mint leaf illustration in deep green tones">
        <div class="badge"><span>100% NATURAL</span><span>FLUORIDE FREE</span></div>
        <p class="net-weight">4.2oz</p>
      </div>
    </div>
    <div class="tube__cap-zone"></div>
  </section>

  <section class="tube tube--back" aria-label="Back of tube">
    <div class="tube__crimp"></div>
    <div class="brand brand--back"><span class="brand__dot"></span>Brisk Hollow</div>
    <div class="back__body">
      <p>Directions:<br>Adults and children 2 years of age and older: Brush teeth thoroughly, preferably after each meal or at least twice a day or as directed by a dentist. Children under 2: consult a dentist.</p>
      <p>Natural Ingredients: vegetable glycerin, de-ionized water, xylitol, calcium carbonate, USDA organic flavor concentrate, sodium coco-sulfate (derived from coconut oil), and carrageenan (extracted from seaweed).</p>
      <p>No parabens, no gluten, no glycols, no SLS, no TEA, no formaldehyde, no artificial flavors, no artificial dye, no artificial sweetener, no dairy, no sorbitol, no saccharines, no peroxides, and no fluoride!</p>
      <p>Made in USA<br>Distribution &amp; Supply Facility:<br>Brisk Hollow LLC<br>2190 Fernwood Ln<br>Alder Falls, MI 48060<br>www.briskhollow.com<br>hello@briskhollow.com</p>
    </div>
    <div class="tube__cap-zone"></div>
  </section>

</main>
</body>
</html>
```